Moulding supply company needs a Door Hanger Design

Door Hanger Design Request from Loft Crafta
www. loftcraftas.ca
We are moulding factory outlet in Toronto. Provide high quality moulding materials with competitive price like crown mouldings, casings, wainscoting, flatstocks, baseboards. We also provide professional installation for our clients. This door hanger will help the home owner easily find a local factory supplier with providing the materials as well as installation.

Detail request for design:
Size: 4”x11”, vertical
Shape: Rectangle

Content:
Front
1. Logo, see attachment(Use the left one, horizontal one)
2. Moulding factory outlet direct sale
3. Supply high quality Crown mouldings, baseboards, casings and wainscotings with competitive price
4. Installation & delivery
#2 content is the most important content, should be bold and readable
#3 can be smaller font compare to #2

Address: 47 West Falcon Ridge Rd, Richmond Hill, ON L3K 2P9
Telephone: 416 730 4215
416 682 1947
Email: info@loftcraftas.ca

Back
Slogan: Convert plain room into designer’s interiors

Telephone: 416 730 4215
416 682 1947
Email: info@loftcraftas.ca

Images:
Front
1. Display our productions for crown mouldings, baseboards, casings and wainscotings, refer to our website www.loftcraftas.ca. (The winner finally we will provide the high resolution images, low resolution please copy from our website so far)
Back
2. Display 4-6 nice images for 1. wainscoting walls 2. feature walls, 3. waffle ceiling like attached below. BUT PLEASE DON'T USE THE IMAGES PROVIDED, THIS IS ONLY A SAMPLE. Please use high resolution images for printing. ALSO PLEASE DON'T LIMIT YOUR CREATIVITY TO USE 4 SQUARES LIKE BELOW IMAGES. Please provide more ideas

Note:
1. Please do the bleeding for final printing production
2. Images have to be high resolution for ready to print
3. Style need to be fresh, clean, easy to read, modern and magazine style
4. Information has to be readable, easy to find, front and back both need to display company address, telephone, email, you can use icon or abbreviation to do these information.

Thanks,
Loft Craftas

```html
<!DOCTYPE html>
<html lang="en">
<head>
<meta charset="utf-8">
<title>Loft Craftas Door Hanger</title>
<link rel="stylesheet" href="https://fonts.googleapis.com/css2?family=Roboto+Condensed:wght@400;500;700&family=Montserrat:wght@300;500&display=swap">
<style>
  :root{
    --stage:#6f6f6f;
    --stage-light:#8c8c8c;
    --blue:#1d4a9c;
    --blue-deep:#163d86;
    --navy-text:#1b3f8f;
    --orange:#ef5a2a;
    --orange-deep:#de4920;
    --white:#ffffff;
    --grey-text:#4c525a;
    --grey-light:#e9e9e9;
  }
  *{margin:0;padding:0;box-sizing:border-box}
  html,body{width:906px;height:1200px;overflow:hidden}
  body{
    background:linear-gradient(135deg,var(--stage) 0%,var(--stage-light) 100%);
    font-family:"Roboto Condensed",Arial,sans-serif;
    position:relative;
  }
  .hanger{
    position:absolute;top:63px;width:357px;height:981px;
    box-shadow:0 6px 14px rgba(0,0,0,.35);
    overflow:hidden;
  }
  .hanger--back{left:83px}
  .hanger--front{left:489px}

  .hanger__head{
    position:absolute;left:0;top:0;width:100%;height:226px;
    background:radial-gradient(ellipse at 75% 30%,#ffffff 0%,#f0f0f0 45%,#c9c9c9 100%);
  }
  .hanger__cut{position:absolute;left:0;top:0}
  .brand{
    position:absolute;left:0;right:0;top:162px;
    display:flex;align-items:center;justify-content:center;gap:10px;
  }
  .brand__mark{width:22px;height:22px;background:var(--orange)}
  .brand__name{
    font-weight:500;font-size:36px;letter-spacing:2px;color:var(--grey-text);line-height:1;
  }
  .brand__tagline{
    position:absolute;left:0;right:0;top:208px;text-align:center;
    font-family:"Montserrat",Arial,sans-serif;font-weight:300;
    font-size:10.5px;letter-spacing:3px;color:var(--grey-text);
  }

  .hanger__body{
    position:absolute;left:0;top:226px;width:100%;height:639px;
    background:
      linear-gradient(160deg,rgba(255,255,255,.05) 0%,rgba(0,0,0,0) 40%,rgba(0,0,0,.08) 100%),
      var(--blue);
  }
  .hanger__foot{
    position:absolute;left:0;top:865px;width:100%;height:116px;
    background:linear-gradient(180deg,var(--orange) 0%,var(--orange-deep) 100%);
    color:var(--white);text-align:center;
  }
  .contact-tab{
    position:absolute;left:113px;top:850px;width:130px;height:28px;
    background:linear-gradient(180deg,#f4f4f4,#cfcfcf);
    color:var(--navy-text);font-size:19px;line-height:28px;text-align:center;z-index:2;
  }
  .contact__phone{
    position:absolute;left:0;right:0;top:21px;font-size:27px;font-weight:500;
    display:flex;align-items:center;justify-content:center;gap:4px;
  }
  .contact__line{
    position:absolute;left:0;right:0;font-size:12px;
    display:flex;align-items:center;justify-content:center;gap:4px;
  }
  .contact__line--address{top:57px}
  .contact__line--email{top:81px}

  /* back side */
  .headline{
    position:absolute;left:0;width:100%;text-align:center;color:var(--white);
    font-weight:400;line-height:1;
  }
  .headline--moulding{top:251px;font-size:72px;letter-spacing:1px}
  .bar{
    position:absolute;background:var(--white);color:var(--navy-text);
    display:flex;align-items:center;
  }
  .bar--outlet{left:22px;top:320px;width:312px;height:31px;padding-left:5px;font-size:25px;letter-spacing:3px}
  .bar--quality{left:64px;top:371px;width:186px;height:34px;justify-content:center;font-size:19px}
  .bar--price{left:64px;top:732px;width:217px;height:34px;justify-content:center;font-size:19px}
  .bar--install{left:22px;top:782px;width:312px;height:41px;justify-content:center;font-size:27px;font-weight:500}
  .connector{position:absolute;background:var(--white)}
  .connector--a{left:178px;top:351px;width:2px;height:20px}
  .connector--b{left:178px;top:766px;width:2px;height:16px}
  .connector--rail{left:41px;top:386px;width:24px;height:363px;border:2px solid var(--white);border-right:none;border-radius:6px 0 0 6px;background:none}
  .badge{position:absolute;left:264px;top:323px}
  .product{
    position:absolute;left:23px;width:68px;height:68px;border-radius:50%;
    border:4px solid var(--orange);
    background:radial-gradient(circle at 40% 40%,#ffffff 0%,#f1f1f1 60%,#dcdcdc 100%);
  }
  .product-label{position:absolute;left:108px;font-size:26px;color:var(--white);line-height:1}

  /* front side */
  .photo-row{position:absolute;left:0;width:100%;height:3px;background:var(--orange)}
  .photo{
    position:absolute;width:84px;height:84px;border-radius:50%;border:4px solid var(--orange);
  }
  .slogan{position:absolute;left:0;width:100%;text-align:center;color:var(--white);line-height:1}
  .slogan--convert{top:369px;font-size:84px}
  .slogan--plain{top:448px;font-size:64px}
  .slogan--into{top:508px;font-size:57px}
  .slogan--designer{top:566px;font-size:64px}
  .slogan--interiors{top:640px;font-size:72px}

  .side-label{
    position:absolute;top:1075px;font-size:40px;color:var(--white);width:357px;text-align:center;
  }
  .side-label--back{left:54px}
  .side-label--front{left:505px}
</style>
</head>
<body>

<section class="hanger hanger--back">
  <div class="hanger__head">
    <svg class="hanger__cut" width="357" height="226" viewBox="0 0 357 226" aria-hidden="true">
      <line x1="105" y1="-4" x2="150" y2="42" stroke="#6f6f6f" stroke-width="13"/>
      <circle cx="179" cy="89" r="55" fill="#6f6f6f"/>
    </svg>
    <div class="brand"><span class="brand__mark"></span><span class="brand__name">LOFT CRAFTAS</span></div>
    <div class="brand__tagline">FOR ALL TYPES OF PROJECTS</div>
  </div>

  <div class="hanger__body"></div>

  <h1 class="headline headline--moulding">MOULDING</h1>
  <div class="bar bar--outlet">FACTORY OUTLET</div>
  <svg class="badge" width="70" height="70" viewBox="0 0 70 70" aria-hidden="true">
    <circle cx="35" cy="35" r="34" fill="var(--orange-deep)"/>
    <circle cx="35" cy="35" r="29" fill="var(--orange)" stroke="#fff" stroke-width="1.5"/>
    <text x="35" y="33" text-anchor="middle" font-family="Roboto Condensed, sans-serif" font-size="14" fill="#fff">DIRECT</text>
    <text x="35" y="51" text-anchor="middle" font-family="Roboto Condensed, sans-serif" font-size="20" font-weight="700" fill="#fff">SALE</text>
  </svg>
  <div class="connector connector--a"></div>
  <div class="bar bar--quality">SUPPLY HIGH QUALITY</div>
  <div class="connector connector--rail"></div>

  <div class="product" style="top:416px" role="img" aria-label="Crown moulding profile samples"></div>
  <div class="product-label" style="top:437px">CROWN MOULDINGS</div>
  <div class="product" style="top:493px" role="img" aria-label="Baseboard profile samples"></div>
  <div class="product-label" style="top:514px">BASEBOARDS</div>
  <div class="product" style="top:572px" role="img" aria-label="Casing profile samples"></div>
  <div class="product-label" style="top:593px">CASINGS</div>
  <div class="product" style="top:651px" role="img" aria-label="Wainscoting profile samples"></div>
  <div class="product-label" style="top:672px">WAINSCOTINGS</div>

  <div class="bar bar--price">WITH COMPETITIVE PRICE</div>
  <div class="connector connector--b"></div>
  <div class="bar bar--install">INSTALLATION &amp; DELIVERY</div>

  <div class="contact-tab">CONTACT US</div>
  <footer class="hanger__foot">
    <div class="contact__phone">
      <svg width="12" height="22" viewBox="0 0 12 22" aria-hidden="true"><path d="M9 1 C3 2 1 7 1 11 C1 15 3 20 9 21 L10 16 C7 15 6 13 6 11 C6 9 7 7 10 6 Z" fill="#fff"/></svg>
      416 730 4215/416 682 1947
    </div>
    <div class="contact__line contact__line--address">
      <svg width="10" height="10" viewBox="0 0 10 10" aria-hidden="true"><circle cx="5" cy="5" r="5" fill="#fff"/><circle cx="5" cy="4.5" r="2" fill="var(--orange)"/></svg>
      47 WEST FALCON RIDGE RD, RICHMOND HILL, ON L3K 2P9
    </div>
    <div class="contact__line contact__line--email">
      <svg width="10" height="10" viewBox="0 0 10 10" aria-hidden="true"><circle cx="5" cy="5" r="5" fill="#fff"/><path d="M2.5 3.5h5v3.2h-5z M2.5 3.5l2.5 2 2.5-2" fill="none" stroke="var(--orange)" stroke-width=".9"/></svg>
      INFO@LOFTCRAFTAS.CA
    </div>
  </footer>
</section>

<section class="hanger hanger--front">
  <div class="hanger__head">
    <svg class="hanger__cut" width="357" height="226" viewBox="0 0 357 226" aria-hidden="true">
      <line x1="105" y1="-4" x2="150" y2="42" stroke="#6f6f6f" stroke-width="13"/>
      <circle cx="179" cy="89" r="55" fill="#6f6f6f"/>
    </svg>
    <div class="brand"><span class="brand__mark"></span><span class="brand__name">LOFT CRAFTAS</span></div>
    <div class="brand__tagline">FOR ALL TYPES OF PROJECTS</div>
  </div>

  <div class="hanger__body"></div>

  <div class="photo-row" style="top:297px"></div>
  <div class="photo" style="left:39px;top:257px;background:radial-gradient(circle at 50% 70%,#c9757a,#6d6a6e 70%)" role="img" aria-label="Bedroom with grey wainscoting wall"></div>
  <div class="photo" style="left:137px;top:257px;background:radial-gradient(circle at 50% 65%,#2e6f7a,#d8dcdd 75%)" role="img" aria-label="Teal feature wall with sofa"></div>
  <div class="photo" style="left:237px;top:257px;background:linear-gradient(180deg,#efe6d3,#c9b996)" role="img" aria-label="White waffle ceiling"></div>

  <div class="slogan slogan--convert">CONVERT</div>
  <div class="slogan slogan--plain">PLAIN ROOM</div>
  <div class="slogan slogan--into">INTO</div>
  <div class="slogan slogan--designer">DESIGNER’S</div>
  <div class="slogan slogan--interiors">INTERIORS</div>

  <div class="photo-row" style="top:762px"></div>
  <div class="photo" style="left:39px;top:722px;background:linear-gradient(180deg,#eeeae4,#b6a998)" role="img" aria-label="White panelled wainscoting room"></div>
  <div class="photo" style="left:137px;top:722px;background:linear-gradient(180deg,#8a7564,#c7c2bb)" role="img" aria-label="Brick feature wall office"></div>
  <div class="photo" style="left:237px;top:722px;background:radial-gradient(circle at 50% 30%,#d9a14a,#4a2a1a 70%)" role="img" aria-label="Wooden coffered ceiling with chandelier"></div>

  <div class="contact-tab">CONTACT US</div>
  <footer class="hanger__foot">
    <div class="contact__phone">
      <svg width="12" height="22" viewBox="0 0 12 22" aria-hidden="true"><path d="M9 1 C3 2 1 7 1 11 C1 15 3 20 9 21 L10 16 C7 15 6 13 6 11 C6 9 7 7 10 6 Z" fill="#fff"/></svg>
      416 730 4215/416 682 1947
    </div>
    <div class="contact__line contact__line--address">
      <svg width="10" height="10" viewBox="0 0 10 10" aria-hidden="true"><circle cx="5" cy="5" r="5" fill="#fff"/><circle cx="5" cy="4.5" r="2" fill="var(--orange)"/></svg>
      47 WEST FALCON RIDGE RD, RICHMOND HILL, ON L3K 2P9
    </div>
    <div class="contact__line contact__line--email">
      <svg width="10" height="10" viewBox="0 0 10 10" aria-hidden="true"><circle cx="5" cy="5" r="5" fill="#fff"/><path d="M2.5 3.5h5v3.2h-5z M2.5 3.5l2.5 2 2.5-2" fill="none" stroke="var(--orange)" stroke-width=".9"/></svg>
      INFO@LOFTCRAFTAS.CA
    </div>
  </footer>
</section>

<div class="side-label side-label--back">BACK</div>
<div class="side-label side-label--front">FRONT</div>

</body>
</html>
```